Keystonery Billboard - Financial Services Company (Investments, Tax Planning and Insurance)

Our new office has a billboard directly above the office building. We'd like something eye-catching with a strong Call to Action, with the main part of the billboard being under 7 words if possible. We'd like you to include a way to get ahold of us (either our website keystoneryllc.example or our phone number 302-418-2907. You may also include in small font something to indicate that we've been serving the area since 1980 (the DE area, the tri-state area, the Marlowe Hollow, etc.)

We offer financial planning, tax planning, and insurance, and we help our clients to focus on their goals and happiness by providing everything they need for lifelong wealth under one roof.

Our logos are attached, we use a triangle logo with green and gray. We use the tagline "discover lasting prosperity" but this does not need to be included.

Potential ideas we have seen from other financial companies-
- the concept that the driver spends more time looking at billboards than planning for their retirement
-something along the lines of "everything you need for your finances is in this building right here" planning, investments, taxes, insurance"
-don't spend your time worrying about retirement, let us help you plan for it
-are you working for your money, or is it working for you?
- retirement takes planning, we're here to help
- ready to retire? talk to us
- need investment advice?
- need help investing?
- crossing your fingers isn't a retirement plan. we can help.
- retiring soon? you need help.

Those are just general ideas, please feel free to be creative.

brand colors:
#00b585
#00b185
#000000
#ffffff
#6d6f75
#6d6f75
#6f7074
#021712
#052e24

```html
<!DOCTYPE html>
<html lang="en">
<head>
<meta charset="utf-8">
<title>Keystonery Billboard</title>
<link href="https://fonts.googleapis.com/css2?family=Montserrat:wght@500;700;800&display=swap" rel="stylesheet">
<style>
  :root {
    --brand-green: #00995e;
    --brand-gray: #5c5d60;
    --band-gray: #6d6f75;
    --white: #ffffff;
    --mint-light: #f4fbf7;
    --mint-mid: #e3f4ee;
    --teal-soft: #a9e1d8;
    --page-bg: #eef0f2;
  }
  * { margin: 0; padding: 0; box-sizing: border-box; }
  html, body {
    width: 1200px;
    height: 900px;
    overflow: hidden;
    background: var(--page-bg);
    font-family: "Montserrat", Arial, sans-serif;
  }
  .canvas {
    position: relative;
    width: 1200px;
    height: 900px;
  }
  .billboard {
    position: absolute;
    left: 20px;
    top: 198px;
    width: 1160px;
    height: 505px;
    overflow: hidden;
    background: linear-gradient(100deg, var(--mint-light) 0%, var(--mint-mid) 55%, var(--teal-soft) 100%);
    box-shadow: 0 10px 30px rgba(0, 0, 0, 0.12);
  }
  .accent-art {
    position: absolute;
    inset: 0;
    width: 1160px;
    height: 505px;
  }
  .brand {
    position: absolute;
    left: 140px;
    top: 58px;
  }
  .brand-name {
    font-weight: 700;
    font-size: 62px;
    line-height: 1;
    color: var(--brand-green);
    letter-spacing: -0.5px;
  }
  .brand-tagline {
    margin-top: 10px;
    font-weight: 500;
    font-size: 12px;
    letter-spacing: 4.4px;
    text-transform: uppercase;
    color: var(--brand-gray);
  }
  .headline {
    position: absolute;
    left: 52px;
    top: 186px;
    font-weight: 800;
    font-size: 58px;
    line-height: 62px;
    text-transform: uppercase;
    color: var(--brand-green);
    letter-spacing: 0.3px;
  }
  .headline .muted { color: var(--brand-gray); }
  .call-band {
    position: absolute;
    left: 0;
    top: 418px;
    width: 680px;
    height: 87px;
    background: var(--band-gray);
    clip-path: polygon(0 0, 100% 0, 93.8% 100%, 0 100%);
    display: flex;
    align-items: center;
    padding-left: 50px;
    color: var(--white);
    font-weight: 800;
  }
  .call-label {
    font-size: 32px;
    letter-spacing: 1px;
    text-transform: uppercase;
  }
  .phone-icon {
    width: 42px;
    height: 42px;
    margin-left: 30px;
    margin-right: 10px;
  }
  .phone-number {
    font-size: 38px;
    letter-spacing: -0.5px;
  }
  .photo-placeholder {
    position: absolute;
    left: 810px;
    top: 150px;
    width: 350px;
    height: 330px;
    background: radial-gradient(ellipse at 55% 55%, #d9a587 0%, #c98f72 30%, rgba(240, 235, 228, 0.9) 62%, rgba(240, 235, 228, 0) 80%);
    opacity: 0.85;
  }
</style>
</head>
<body>
<main class="canvas">
  <section class="billboard">
    <svg class="accent-art" viewBox="0 0 1160 505" aria-hidden="true">
      <polygon points="865,505 1085,0 1160,0 1160,505" fill="var(--brand-green)"/>
    </svg>

    <div class="photo-placeholder" role="img" aria-label="Photo of an open hand holding a glowing rising bar chart"></div>

    <header class="brand">
      <div class="brand-name">Keystonery</div>
      <div class="brand-tagline">discover lasting prosperity</div>
    </header>

    <h1 class="headline">
      Retirement <span class="muted">Takes</span><br>
      <span class="muted">Planning,</span> We're<br>
      Here to Help
    </h1>

    <div class="call-band">
      <span class="call-label">Call Us</span>
      <svg class="phone-icon" viewBox="0 0 42 42" aria-hidden="true">
        <circle cx="21" cy="21" r="20" fill="var(--white)"/>
        <path d="M14.5 11.5c1-.6 2.2-.4 2.9.6l2 3c.6.9.4 2-.3 2.7l-1.3 1.2c.9 2.2 2.5 3.9 4.7 4.9l1.3-1.3c.7-.7 1.9-.8 2.7-.2l3 2.1c1 .7 1.2 2 .5 2.9l-1.2 1.6c-.8 1-2.2 1.5-3.5 1.1C18.6 28 13.9 23.3 12 16.9c-.4-1.3 0-2.7 1.1-3.5z" fill="var(--band-gray)"/>
      </svg>
      <span class="phone-number">302-418-2907</span>
    </div>
  </section>
</main>
</body>
</html>
```